Audio-Visual & Video Communications Business Requires a Cutting-edge Business Card Design

LinkVerra is a new Audio-Visual & Video Communications company in Cape Town, South Africa that is looking for a cutting-edge business card design. We sell these products to the Corporate, Education & Hospitality markets and will also host an Online Shop for companies and individuals to purchase our products online.

We are already using the following two colours in our logo and draft website. Please incorporate these colours into the design. Please note that our website is still in the design stage if you need to visit it. Green #a0ce4e & Dark Grey #333333.

Hi,

Please note that I have uploaded our logo in an .eps format.

Target Market(s)

Corporate Companies, Education Institutions & Hospitality Markets

Industry/Entity Type

Business

Requirements
Nice to have
• It would be great if you could incorporate the services that we offer.

1. Consultation & Design
2. Project Management
3. Supply & Installation
4. Onsite Support Personal
5. Online Shop

```html
<!DOCTYPE html>
<html lang="en">
<head>
<meta charset="utf-8">
<title>LinkVerra Business Card</title>
<link rel="stylesheet" href="https://fonts.googleapis.com/css2?family=Open+Sans:wght@400;700&family=Arimo:wght@400&display=swap">
<style>
  :root {
    --page-bg: #808080;
    --band-grey: #4a4a4a;
    --card-white: #ffffff;
    --brand-green: #76b900;
    --text-dark: #444444;
    --text-mid: #666666;
    --text-light: #ffffff;
  }
  * { margin: 0; padding: 0; box-sizing: border-box; }
  html, body {
    width: 1200px;
    height: 900px;
    overflow: hidden;
    background: var(--page-bg);
  }
  .card {
    position: absolute;
    left: 285px;
    top: 259px;
    width: 631px;
    height: 385px;
    background: var(--card-white);
    border-radius: 22px 22px 0 0;
    overflow: hidden;
  }
  .card-header {
    height: 130px;
    background: var(--band-grey);
    text-align: center;
    color: var(--text-light);
  }
  .holder-name {
    padding-top: 18px;
    font-family: "Open Sans", sans-serif;
    font-weight: 400;
    font-size: 27px;
    line-height: 36px;
    color: var(--brand-green);
  }
  .contact-line {
    font-family: "Arimo", sans-serif;
    font-size: 19px;
    line-height: 22px;
  }
  .contact-line.address { margin-top: 9px; }
  .brand-mark {
    position: absolute;
    left: 123px;
    top: 178px;
    width: 80px;
    height: 80px;
    border-radius: 50%;
    background: var(--brand-green);
  }
  .brand-name {
    position: absolute;
    left: 37px;
    top: 282px;
    width: 260px;
    text-align: center;
    font-family: "Open Sans", sans-serif;
    font-weight: 700;
    font-size: 33px;
    line-height: 40px;
    color: var(--text-dark);
  }
  .website {
    position: absolute;
    left: 36px;
    top: 344px;
    font-family: "Arimo", sans-serif;
    font-size: 21px;
    color: var(--text-dark);
  }
  .divider {
    position: absolute;
    left: 364px;
    top: 231px;
    width: 3px;
    height: 154px;
    background: var(--brand-green);
  }
  .services {
    position: absolute;
    left: 392px;
    top: 234px;
    list-style: none;
    font-family: "Open Sans", sans-serif;
    font-weight: 700;
    font-size: 16px;
    line-height: 28.5px;
    color: var(--text-mid);
  }
</style>
</head>
<body>
  <article class="card">
    <header class="card-header">
      <h1 class="holder-name">Daniel Marsh</h1>
      <p class="contact-line address">42 Kestrel Lane • Cape Town - South Africa</p>
      <p class="contact-line phone">555-214-7730</p>
    </header>
    <div class="brand-mark"></div>
    <div class="brand-name">LinkVerra</div>
    <p class="website">www.linkverra.com</p>
    <div class="divider"></div>
    <ul class="services">
      <li>Consultation &amp; Design</li>
      <li>Project Management</li>
      <li>Supply &amp; Installation</li>
      <li>Onsite Support Personal</li>
      <li>Online Shop</li>
    </ul>
  </article>
</body>
</html>
```